Need webdesign for service company that provides Car hiring service and transit service

We need a web design for a company that provides airport transit services and transport services including Limo, Corporate cars, Disability transit, Family transit service. We need is a simple and professional design.

Below is site which we like and also offer the same service http://www.ridelarkway.com.au/
Updates

Project Deadline Extended
Reason: Waiting for the Feedback from multiple stakeholders. Need the time to select and approve the design

Target Market(s)

Tourism, Travel

Industry/Entity Type

Airport

Number of Pages Required

3 page

Font styles to use
Decorative
Script

Requirements
Must have
• Simple and Professional, Site we like http://www.ridelarkway.com.au/ and also need to mobile friendly
Should not have
• Shouldn't have too many images

```html
<!DOCTYPE html>
<html lang="en">
<head>
<meta charset="utf-8">
<title>Ridewell — Private &amp; Business Transport</title>
<link href="https://fonts.googleapis.com/css2?family=Mulish:wght@300;400;600;700&display=swap" rel="stylesheet">
<style>
  :root {
    --ink: #111111;
    --black: #000000;
    --white: #ffffff;
    --slate: #6e6869;
    --button-grey: #6c6667;
    --muted: #8a8a8a;
    --body-text: #9a9a9a;
    --footer-bg: #f1f1f1;
    --footer-line: #dddddd;
    --hero-top: #5a5f69;
    --hero-bottom: #3a3d44;
  }
  * { box-sizing: border-box; margin: 0; padding: 0; }
  html, body { width: 1014px; height: 1200px; overflow: hidden; background: var(--white); }
  body { position: relative; font-family: "Mulish", Arial, sans-serif; color: var(--ink); }

  .site-header { position: absolute; left: 0; top: 0; width: 1014px; height: 84px; background: var(--white); }
  .brand { position: absolute; left: 100px; top: 26px; display: flex; align-items: center; gap: 10px; }
  .brand-square { width: 30px; height: 30px; border: 2px solid var(--ink); }
  .brand-name { font-size: 28px; font-weight: 400; letter-spacing: 0.5px; color: var(--ink); }
  .header-tools { position: absolute; right: 104px; top: 30px; display: flex; align-items: center; gap: 24px; }
  .header-tools svg { display: block; }

  .hero { position: absolute; left: 0; top: 84px; width: 1014px; height: 503px; }
  .hero-photo { position: absolute; inset: 0; background: radial-gradient(ellipse at 50% 45%, #6d6f76 0%, var(--hero-top) 45%, var(--hero-bottom) 100%); }
  .hero-title { position: absolute; left: 0; width: 100%; top: 79px; text-align: center; color: var(--white); font-weight: 400; font-size: 56px; line-height: 1; letter-spacing: 0.5px; }
  .hero-subtitle { position: absolute; left: 0; width: 100%; top: 137px; text-align: center; color: var(--white); font-weight: 400; font-size: 24px; line-height: 1; letter-spacing: 0.5px; }

  .quote-frame { position: absolute; left: 304px; top: 234px; width: 406px; height: 184px; border: 2px solid rgba(255,255,255,0.75); border-top: none; }
  .quote-frame::before, .quote-frame::after { content: ""; position: absolute; top: 0; height: 2px; background: rgba(255,255,255,0.75); }
  .quote-frame::before { left: -2px; width: 86px; }
  .quote-frame::after { right: -2px; width: 84px; }
  .quote-label { position: absolute; left: 0; width: 100%; top: -10px; text-align: center; color: var(--white); font-size: 17px; font-weight: 400; letter-spacing: 0.3px; }
  .quote-field { position: absolute; left: 35px; width: 347px; height: 32px; background: var(--white); border: none; padding: 0 12px; font-family: inherit; font-size: 11.5px; color: #555; display: flex; align-items: center; }
  .quote-field.origin { top: 41px; }
  .quote-field.destination { top: 82px; }
  .quote-submit { position: absolute; left: 35px; top: 124px; width: 347px; height: 32px; background: var(--button-grey); color: var(--white); font-size: 15px; display: flex; align-items: center; justify-content: center; letter-spacing: 0.3px; }

  .service-card { position: absolute; top: 606px; height: 233px; text-align: center; color: var(--white); }
  .service-card.airport { left: 99px; width: 265px; background: var(--black); }
  .service-card.why-us { left: 373px; width: 264px; background: var(--slate); }
  .service-card.support { left: 645px; width: 265px; background: var(--black); }
  .service-icon { position: absolute; left: 0; width: 100%; top: 24px; height: 60px; display: flex; justify-content: center; align-items: center; }
  .service-title { position: absolute; left: 20px; right: 20px; top: 93px; font-size: 16px; font-weight: 400; line-height: 19px; letter-spacing: 0.3px; }
  .service-text { position: absolute; left: 30px; right: 30px; font-size: 10.5px; line-height: 14px; color: #a8a8a8; font-weight: 400; }
  .why-us .service-text { color: #c4c0c0; }
  .airport .service-text { top: 135px; }
  .why-us .service-text, .support .service-text { top: 119px; }
  .service-button { position: absolute; left: 50%; transform: translateX(-50%); top: 173px; width: 101px; height: 28px; border: 1px solid var(--white); font-size: 11px; display: flex; align-items: center; justify-content: center; }

  .news-heading { position: absolute; left: 99px; top: 911px; font-size: 22px; font-weight: 400; letter-spacing: 0.3px; }
  .news-item { position: absolute; top: 956px; width: 250px; }
  .news-item:nth-of-type(1) { left: 101px; }
  .news-item:nth-of-type(2) { left: 388px; }
  .news-item:nth-of-type(3) { left: 687px; width: 230px; }
  .news-date { font-size: 12px; color: #6f6f6f; line-height: 16px; }
  .news-title { font-size: 14.5px; font-weight: 400; line-height: 20px; margin-top: 4px; }
  .news-excerpt { font-size: 10.5px; line-height: 17.5px; color: var(--body-text); margin-top: 6px; }
  .news-more { font-size: 11px; color: #555; margin-top: 5px; }

  .site-footer { position: absolute; left: 0; top: 1142px; width: 1014px; height: 58px; background: var(--footer-bg); border-top: 1px solid var(--footer-line); text-align: center; font-size: 12px; color: #666; padding-top: 18px; }
</style>
</head>
<body>
  <header class="site-header">
    <div class="brand">
      <span class="brand-square"></span>
      <span class="brand-name">RIDEWELL</span>
    </div>
    <nav class="header-tools" aria-label="Site tools">
      <svg width="28" height="18" viewBox="0 0 28 18" aria-label="Menu"><rect y="0" width="28" height="3" fill="#111"/><rect y="7.5" width="28" height="3" fill="#111"/><rect y="15" width="28" height="3" fill="#111"/></svg>
      <svg width="20" height="20" viewBox="0 0 24 24" aria-label="Call"><path fill="#777" d="M6.6 10.8c1.4 2.8 3.8 5.1 6.6 6.6l2.2-2.2c.3-.3.7-.4 1-.2 1.1.4 2.3.6 3.6.6.6 0 1 .4 1 1V20c0 .6-.4 1-1 1C10.6 21 3 13.4 3 4c0-.6.4-1 1-1h3.5c.6 0 1 .4 1 1 0 1.3.2 2.5.6 3.6.1.3 0 .7-.2 1l-2.3 2.2z"/></svg>
      <svg width="20" height="20" viewBox="0 0 20 20" aria-label="Search"><circle cx="8" cy="8" r="6" fill="none" stroke="#777" stroke-width="2.5"/><line x1="12.5" y1="12.5" x2="18" y2="18" stroke="#777" stroke-width="2.8" stroke-linecap="round"/></svg>
    </nav>
  </header>

  <section class="hero">
    <div class="hero-photo" role="img" aria-label="Photo of business passengers working in the back seat of a chauffeured car"></div>
    <h1 class="hero-title">PRIVATE &amp; BUSINESS</h1>
    <p class="hero-subtitle">PERSONALISED TRANSPORT SERVICES</p>
    <form class="quote-frame">
      <p class="quote-label">GET INSTANT QUOTE</p>
      <div class="quote-field origin">Origin (Public location or Exact address )</div>
      <div class="quote-field destination">Destination (Public location or Exact address )</div>
      <div class="quote-submit">SUBMIT</div>
    </form>
  </section>

  <article class="service-card airport">
    <div class="service-icon">
      <svg width="92" height="40" viewBox="0 0 92 40" fill="none" stroke="#fff" stroke-width="2.5" stroke-linejoin="round">
        <path d="M4 28 V20 Q4 15 10 14 L20 13 L26 4 H62 L70 13 L84 15 Q89 16 89 21 V28 H74"/>
        <path d="M30 28 H58"/>
        <path d="M4 28 H14"/>
        <circle cx="22" cy="29" r="6"/><circle cx="66" cy="29" r="6"/>
        <path d="M29 7 V13 M41 7 V13 M53 7 V13"/>
      </svg>
    </div>
    <h2 class="service-title">AIRPORT TRANSIT<br>SERVICES</h2>
    <p class="service-text">Proin nulla arcu nonummy luctus dictum eget fermentum et lorem</p>
    <div class="service-button">READ MORE</div>
  </article>

  <article class="service-card why-us">
    <div class="service-icon">
      <svg width="46" height="60" viewBox="0 0 46 60" fill="none" stroke="#fff" stroke-width="2.3" stroke-linejoin="round">
        <path d="M8 6 L23 1 L38 6 V12 H8 Z"/>
        <path d="M12 12 V20 Q23 30 34 20 V12"/>
        <path d="M2 58 V40 Q2 32 12 30 H34 Q44 32 44 40 V58 Z"/>
        <path d="M14 52 L32 36"/>
        <path d="M10 58 V52 H36"/>
      </svg>
    </div>
    <h2 class="service-title">WHY CHOOSE US</h2>
    <p class="service-text">Proin nulla arcu nonummy luctus dictum eget fermentum et lorem Nunc porta convallis pede</p>
    <div class="service-button">READ MORE</div>
  </article>

  <article class="service-card support">
    <div class="service-icon">
      <svg width="50" height="50" viewBox="0 0 50 50" fill="none" stroke="#fff" stroke-width="2.3" stroke-linejoin="round">
        <circle cx="30" cy="20" r="17"/>
        <path d="M6 18 L12 12 L19 20 L15 24 Q19 31 26 35 L30 31 L38 38 L32 44 Q18 42 6 18 Z" fill="#000"/>
        <text x="30" y="25" text-anchor="middle" font-family="Mulish, Arial, sans-serif" font-size="13" font-weight="700" fill="#fff" stroke="none">24</text>
      </svg>
    </div>
    <h2 class="service-title">24/7 SUPPORT</h2>
    <p class="service-text">Proin nulla arcu nonummy luctus dictum eget fermentum et lorem Nunc porta convallis pede</p>
    <div class="service-button">READ MORE</div>
  </article>

  <section class="news">
    <h2 class="news-heading">NEWS &amp; BLOGS</h2>
    <article class="news-item">
      <p class="news-date">24 April 2017</p>
      <h3 class="news-title">Sociosqu ad litora torquent</h3>
      <p class="news-excerpt">per conubia nostra per inceptos hymenaeos Proin nulla arcu nonummy luctus dictum eget fermentum et lorem Nunc porta convallis pede</p>
      <p class="news-more">READ MORE</p>
    </article>
    <article class="news-item">
      <p class="news-date">14 April 2017</p>
      <h3 class="news-title">Praesent elementum elit</h3>
      <p class="news-excerpt">per conubia nostra per inceptos hymenaeos Proin nulla arcu nonummy luctus dictum eget fermentum et lorem Nunc porta convallis pede</p>
      <p class="news-more">READ MORE</p>
    </article>
    <article class="news-item">
      <p class="news-date">10 April 2017</p>
      <h3 class="news-title">Etiam eleifend metus vitae</h3>
      <p class="news-excerpt">per conubia nostra per inceptos hymenaeos Proin nulla arcu nonummy luctus dictum eget fermentum et lorem Nunc porta convallis pede</p>
      <p class="news-more">READ MORE</p>
    </article>
  </section>

  <footer class="site-footer">© 2017 Company Name&nbsp; All right reserved&nbsp; Term of Use</footer>
</body>
</html>
```